Varnik Holdings — Business Card Design Brief
Overview
Design a double-sided business card for Varnik Holdings that highlights our two service arms: Varnik Communications (telecommunications) and Varnik Energy (business energy solutions). The card should feel smart and stand out when handed to clients.

Objectives
Showcase our areas of specialty clearly.
Reflect the overall Varnik / Varnik Holdings brand while acknowledging both arms.
Explore using both logos (Communications + Energy) or one unified logo, depending on the design.

Deliverables
One double-sided business card design (front + back).

Content & Copy
Front (preferred): Logo: Varnik / Varnik Holdings
Descriptor: Business Communications | Business Energy
Back:My contact details and company details
Core products: Business Mobile • Telephony • Internet • Business Energy Solutions

Brand & Visual Direction
We have a group logo currently tailored more toward telecoms, plus a separate Varnik Energy logo.
Please explore layouts that use both logos or just one, whichever works best.
Color: I wouldn't mind seeing an option using our the Blue/Purple gradient from our website (varnik-example.co.uk), but also open to non-gradient approaches and other colours..

Overall look: Smart, modern, and distinctive.
Format & Print Specs
Double-sided business card format. (Use a standard size

Must-Haves
Front: Varnik wording or Varnik Holdings wording with atleast 1 logo also on front “Business Communications | Business Energy.”

Back: Contact + company details and core products.
A design that stands out while remaining professional.

Nice-to-Have Options
A gradient version using our site’s Blue/Purple gradient.
A non-gradient version.
A dual-logo treatment versus a single-logo treatment.

Thanks
Owen

```html
<!DOCTYPE html>
<html lang="en">
<head>
<meta charset="utf-8">
<title>Varnik Holdings — Business Card</title>
<link rel="stylesheet" href="https://fonts.googleapis.com/css2?family=Montserrat:wght@400;500;700;800&display=swap">
<style>
  :root {
    --stage: #e9e9ec;
    --navy: #27215f;
    --ink: #1f1a52;
    --white: #ffffff;
    --green: #3aa845;
    --lime: #c8d42c;
    --blue: #2f6fc4;
    --sky: #2a95d6;
    --text: #2a2a3a;
  }
  * { box-sizing: border-box; margin: 0; padding: 0; }
  html, body { width: 1200px; height: 875px; overflow: hidden; }
  body {
    background: var(--stage);
    font-family: "Montserrat", sans-serif;
    display: flex;
    align-items: center;
    justify-content: center;
    gap: 40px;
  }
  .card {
    position: relative;
    width: 540px;
    height: 310px;
    border-radius: 18px;
    overflow: hidden;
    box-shadow: 0 10px 30px rgba(0,0,0,0.18);
  }

  /* Front */
  .card--front { background: var(--navy); color: var(--white); }
  .front__brand {
    position: absolute;
    left: 0; right: 0; top: 92px;
    display: flex;
    align-items: center;
    justify-content: center;
    gap: 18px;
  }
  .front__mark { width: 66px; height: 66px; border-radius: 50%; background: var(--green); }
  .front__name { font-weight: 800; font-size: 64px; letter-spacing: 1px; line-height: 1; }
  .front__descriptor {
    position: absolute; left: 0; right: 0; top: 178px;
    text-align: center; font-size: 13px; font-weight: 500; letter-spacing: 0.5px;
  }
  .front__products {
    position: absolute; left: 0; right: 0; bottom: 34px;
    display: flex; justify-content: center; gap: 14px;
    font-size: 12px; font-weight: 400; list-style: none;
  }
  .front__products li::before {
    content: ""; display: inline-block; width: 6px; height: 6px;
    border-radius: 50%; background: var(--lime); margin-right: 6px; vertical-align: middle;
  }

  /* Back */
  .card--back { background: var(--white); color: var(--text); }
  .back__brand {
    position: absolute; left: 44px; top: 120px;
    display: flex; align-items: center; gap: 12px;
  }
  .back__mark { width: 38px; height: 38px; border-radius: 50%; background: var(--blue); }
  .back__name { font-weight: 800; font-size: 36px; color: var(--ink); line-height: 1; }
  .back__divider {
    position: absolute; left: 250px; top: 66px; width: 1.5px; height: 150px; background: var(--ink);
  }
  .back__details { position: absolute; left: 268px; top: 62px; }
  .person__name { font-weight: 800; font-size: 22px; color: var(--ink); }
  .person__title { font-size: 11.5px; margin-top: 2px; }
  .company__address { font-size: 11.5px; margin-top: 10px; line-height: 1.4; font-style: normal; }
  .contact { list-style: none; margin-top: 8px; }
  .contact li { display: flex; align-items: center; gap: 8px; font-size: 11.5px; line-height: 1.7; }
  .contact svg { width: 11px; height: 11px; fill: var(--sky); flex: none; }
  .back__band { position: absolute; left: 0; bottom: 0; width: 540px; height: 24px; }
</style>
</head>
<body>
  <section class="card card--front" aria-label="Card front">
    <div class="front__brand">
      <span class="front__mark"></span>
      <span class="front__name">VARNIK</span>
    </div>
    <p class="front__descriptor">Business Communications | Business Energy</p>
    <ul class="front__products">
      <li>Business Mobile</li>
      <li>Telephony</li>
      <li>Internet</li>
      <li>Business Energy Solutions</li>
    </ul>
  </section>

  <section class="card card--back" aria-label="Card back">
    <div class="back__brand">
      <span class="back__mark"></span>
      <span class="back__name">VARNIK</span>
    </div>
    <div class="back__divider"></div>
    <div class="back__details">
      <h1 class="person__name">Owen Calder</h1>
      <p class="person__title">Business Development Manager</p>
      <address class="company__address">45 Kestrel<br>Park, London, UK</address>
      <ul class="contact">
        <li><svg viewBox="0 0 24 24"><path d="M6.6 10.8a15 15 0 0 0 6.6 6.6l2.2-2.2c.3-.3.7-.4 1-.2 1.1.4 2.3.6 3.6.6.6 0 1 .4 1 1V20c0 .6-.4 1-1 1A17 17 0 0 1 3 4c0-.6.4-1 1-1h3.5c.6 0 1 .4 1 1 0 1.3.2 2.5.6 3.6.1.3 0 .7-.2 1z"/></svg>+44 (0)1632 960 418</li>
        <li><svg viewBox="0 0 24 24"><path d="M2 5h20v14H2z M2 5l10 8 10-8" fill="none" stroke="#2a95d6" stroke-width="2.4"/></svg>owen.calder@varnik-example.co.uk</li>
        <li><svg viewBox="0 0 24 24"><circle cx="12" cy="12" r="10"/></svg>www.varnik-example.co.uk</li>
      </ul>
    </div>
    <svg class="back__band" viewBox="0 0 540 24" preserveAspectRatio="none" aria-hidden="true">
      <rect x="0" y="10" width="540" height="14" fill="#27215f"/>
      <polygon points="300,0 540,0 540,10 290,10" fill="#2a95d6"/>
    </svg>
  </section>
</body>
</html>
```